Trade Show booth design

I need the following designs for my trade booth:
1. backboard design 3m Wx2mH
2. Tressle table, tablecloth front panel design 1800W x 740mmH
3. Pop-up banner. I have included our logos and some design content ideas:
Headline:
"Cleaner Classrooms. Safer Schools."
Subheadline:
"Specialist Cleaning Solutions for Education Facilities"
Key Points to Grab Attention:
Healthy Environments: Create hygienic, safe learning spaces for students and staff with our expert cleaning services.
Tailored to Your Needs: Custom cleaning plans for classrooms, labs, libraries, and sports facilities.
Affordable Excellence: Premium results without premium costs – tailored plans mean you only pay for what you need.
Safety First: All staff are trained, highly vetted, and hold current Working with Children Checks (WWCC).
Eco-Conscious Cleaning: Using non-toxic, eco-friendly products certified for health and safety.
What Schools Really Need:
Reliability: Consistent, high-quality cleaning from a trusted provider.
Cost-Effectiveness: Solutions that fit tight budgets while maintaining high standards.
Expertise: Over 30 years of experience in education facility cleaning.
Disinfection Services: Focus on high-touch areas to reduce the spread of germs and ensure peace of mind.
Visual Elements:
Images of bright, clean classrooms, a happy teacher welcoming students, or students collaborating in a spotless library.
Icons representing safety (shield), hygiene (sparkling star), and eco-friendliness (leaf).
Your logo with the tagline: "Trusted by Queensland Schools Since 1995."
Call-to-Action:
"Visit us to discuss your school’s cleaning needs and book a FREE consultation."
Include contact details: Phone: 1300 594 316 | Website: www.brightmorefacility.com.au
Target Market(s)
Education sector
Industry/Entity Type
Commercial Cleaning
Font styles to use
Other font styles liked:
- Montserrat
Look and feel

```html
<!DOCTYPE html>
<html lang="en">
<head>
<meta charset="utf-8">
<title>Brightmore Facility Cleaning – Education Backboard</title>
<link rel="stylesheet" href="https://fonts.googleapis.com/css2?family=Montserrat:wght@400;500;600;800&family=Roboto+Condensed:wght@700&display=swap">
<style>
  :root {
    --navy: #1b3f62;
    --navy-text: #1a3d60;
    --ink: #111820;
    --white: #ffffff;
    --stage: #cde1fb;
    --silver: #c9ccd1;
    --silver-light: #eceef1;
    --mist: #d9ecf6;
  }
  * { margin: 0; padding: 0; box-sizing: border-box; }
  html, body { width: 1200px; height: 600px; overflow: hidden; }
  body { background: var(--stage); font-family: "Montserrat", sans-serif; }

  .board {
    position: absolute; left: 150px; top: 0;
    width: 900px; height: 600px;
    background: var(--white); overflow: hidden;
  }
  .board-shapes { position: absolute; inset: 0; }

  .brand {
    position: absolute; top: 44px; left: 0; width: 100%;
    display: flex; justify-content: center; align-items: center; gap: 12px;
  }
  .brand-dot { width: 26px; height: 26px; border-radius: 50%; background: var(--navy); }
  .brand-name {
    font-weight: 600; font-size: 26px; letter-spacing: 1px;
    color: var(--navy-text); text-transform: uppercase;
  }

  .headline {
    position: absolute; top: 112px; left: 0; width: 100%;
    text-align: center; font-weight: 800; font-size: 48px; line-height: 41px;
    color: var(--navy-text); text-transform: uppercase;
  }

  .subheadline {
    position: absolute; top: 204px; left: 0; width: 100%;
    text-align: center; font-weight: 500; font-size: 20.5px; line-height: 26px;
    color: var(--navy-text);
  }

  .feature {
    position: absolute; top: 334px;
    font-size: 16px; line-height: 20px; color: var(--ink);
  }
  .feature strong { font-weight: 800; }
  .feature-years { left: 134px; }
  .feature-trust { left: 363px; }
  .feature-eco { left: 610px; }

  .cta {
    position: absolute; top: 476px; right: 43px;
    text-align: right; font-size: 16px; line-height: 20px; color: var(--white);
  }
  .website {
    position: absolute; top: 522px; right: 43px;
    font-size: 29px; line-height: 40px; color: var(--white); letter-spacing: 0.2px;
  }
  .phone {
    position: absolute; left: 32px; top: 521px; width: 287px; height: 43px;
    border-radius: 22px;
    background: linear-gradient(90deg, var(--silver) 0%, var(--silver-light) 55%, var(--silver) 100%);
    display: flex; align-items: center; justify-content: center; gap: 6px;
    font-family: "Roboto Condensed", sans-serif; font-weight: 700; font-size: 37px;
    color: var(--navy-text);
  }
</style>
</head>
<body>
  <main class="board">
    <svg class="board-shapes" width="900" height="600" viewBox="0 0 900 600" aria-hidden="false">
      <defs>
        <linearGradient id="mist-flow" x1="0" y1="0" x2="1" y2="0">
          <stop offset="0" stop-color="#cfe6f3" stop-opacity="0.9"/>
          <stop offset="0.5" stop-color="#e6f2f9" stop-opacity="0.6"/>
          <stop offset="1" stop-color="#cfe6f3" stop-opacity="0.8"/>
        </linearGradient>
        <linearGradient id="silver-sweep" x1="0" y1="0" x2="1" y2="0">
          <stop offset="0" stop-color="#bfc3c8"/>
          <stop offset="0.6" stop-color="#eef0f2"/>
          <stop offset="1" stop-color="#c4c8cd"/>
        </linearGradient>
      </defs>

      <path role="img" aria-label="Soft flowing light blue wave texture"
            fill="url(#mist-flow)"
            d="M0,220 C150,260 260,340 420,300 C600,250 720,150 900,130 L900,360 C760,340 640,410 480,420 C300,430 160,360 0,320 Z"/>

      <path class="band-subheadline" fill="url(#silver-sweep)"
            d="M92,204 L816,204 C810,220 806,230 796,230 L83,230 C84,218 86,208 92,204 Z"/>

      <path class="sweep-left" fill="url(#silver-sweep)"
            d="M0,315 C40,420 150,500 300,508 C400,512 520,480 610,440 C520,470 420,500 300,496 C170,490 60,440 0,384 Z"/>
      <path class="sweep-right" fill="url(#silver-sweep)"
            d="M640,418 C720,400 820,400 900,460 L900,481 C860,440 780,410 700,412 Z"/>

      <path class="band-navy" fill="var(--navy)"
            d="M0,384 C70,450 170,510 300,512 C430,512 580,420 760,412 C830,410 880,450 900,481 L900,600 L0,600 Z"/>

      <g class="icon-badges">
        <circle cx="175" cy="291" r="40" fill="#eef0f3"/>
        <circle cx="175" cy="291" r="34" fill="var(--navy)" role="img" aria-label="Handshake icon"/>
        <circle cx="402" cy="291" r="40" fill="#eef0f3"/>
        <circle cx="402" cy="291" r="34" fill="var(--navy)" role="img" aria-label="Trusted professional with stars icon"/>
        <circle cx="650" cy="291" r="40" fill="#eef0f3"/>
        <circle cx="650" cy="291" r="34" fill="var(--navy)" role="img" aria-label="Eco leaf icon"/>
      </g>
    </svg>

    <header class="brand">
      <span class="brand-dot"></span>
      <span class="brand-name">Brightmore Facility</span>
    </header>

    <h1 class="headline">Creating Cleaner,<br>Safer Learning Environments</h1>
    <p class="subheadline">Specialists in Education Facility Cleaning &amp; Eco-Friendly Services</p>

    <p class="feature feature-years">Over <strong>30 years</strong><br>of expertise in<br>commercial cleaning.</p>
    <p class="feature feature-trust">Trusted by <strong>schools,<br>universities, and TAFEs</strong><br>across Queensland.</p>
    <p class="feature feature-eco"><strong>100% Carbon Neutral<br>and Eco-Certified</strong><br>Services.</p>

    <p class="cta">Visit us to discuss your school’s cleaning needs<br>and book a FREE consultation.</p>
    <p class="website">www.brightmorefacility.com.au</p>

    <div class="phone">
      <svg width="14" height="28" viewBox="0 0 14 28" aria-hidden="true">
        <rect x="1" y="1" width="12" height="26" rx="2.5" fill="none" stroke="var(--navy)" stroke-width="2"/>
        <rect x="4.5" y="23" width="5" height="1.6" fill="var(--navy)"/>
      </svg>
      <span>1300 594 316</span>
    </div>
  </main>
</body>
</html>
```